freshen up existing wordpress site

We wish to re-implement our current wordpress website www.vornimax.com/web2.

The content, structure and menus of the website should remain the same, but style updated to a more fresh/contemporary layout. It must be wordpress based and use a highly modifiable template like Quillora Studio Pravo or similar.

Permalinks must be exactly as the old ones.

Landing page must contain a slider for images and movies, plus a little text. There is no requirement for a tab-style as seem on the current website.

The final result shall be transferred to a fresh multisite installation of wordpress, we will provide login for access later. If another method is better/more preferred, please comment and we can take it from there.

The two graphics on http://vornimax.com/web2/gridmarshal-product-details/ should be re-done to look more 'clean and professional' and look less powerpoint'ish. We will need the vectorfiles for edits later on. Color scheme is open, whatever matches with the the website style.

We work in a engineering-heavy B2B environment, so slightly conservative/boring styles; no 'pop smartness'. competitors websites looks like this:
- http://www.lumivex.com/
- http://www.corbantix.com/
- https://www.ostrivel.com/products/ic_nanometer_design/
- https://www.quendor-da.com/

Website background should be white for easy image implementation. Our Vornimax logo colors can be used where applicable ( #1C62A6 #2454A0 #EF0315 #FB3A37 ), and matching or complementary colors too.

Use Sans Serif fonts like googles or something like http://www.glyphbarrow.com/fonts/noto-sans .

Target Market(s)

semiconductor industry

Number of Pages Required

5+ page

Font styles to use
Sans Serif

Requirements
Must have
• see above
Nice to have
• see above
Should not have
• not defined.

```html
<!DOCTYPE html>
<html lang="en">
<head>
<meta charset="utf-8">
<title>Vornimax</title>
<link rel="stylesheet" href="https://fonts.googleapis.com/css2?family=Lato:wght@400;700&family=Play:wght@400;700&display=swap">
<style>
:root{
  --navy:#0d1f5f;
  --blue:#1c62a6;
  --red:#ee1c25;
  --text:#222;
  --grey-bg:#f7f7f7;
  --rule:#cfcfcf;
}
*{box-sizing:border-box;margin:0;padding:0}
html,body{width:1126px;height:1200px;overflow:hidden;background:#fff;font-family:"Lato",sans-serif;color:var(--text)}
.canvas{position:relative;width:1126px;height:1200px}
.abs{position:absolute}

/* header */
.site-header{position:absolute;left:0;top:0;width:1126px;height:112px;background:#fff;border-top:4px solid var(--navy)}
.contact-mail{position:absolute;left:699px;top:9px;font-size:13px;color:#333;display:flex;align-items:center;gap:6px}
.contact-phone{position:absolute;left:867px;top:0;width:167px;height:28px;background:var(--navy);border-radius:0 0 26px 26px;color:#fff;font-size:15px;font-weight:700;display:flex;align-items:center;justify-content:center;gap:6px}
.brand{position:absolute;left:75px;top:48px;display:flex;align-items:center;gap:8px;font-family:"Play",sans-serif;font-weight:700;font-size:38px;color:var(--navy);letter-spacing:-1px}
.brand-square{width:34px;height:34px;background:var(--blue)}
.main-nav{position:absolute;top:72px;left:482px;display:flex;align-items:center;font-family:"Play",sans-serif;font-weight:700;font-size:17px;color:#333}
.main-nav span{padding:0 19px;border-left:1px solid #ddd;line-height:18px}
.main-nav .home{border:none;padding:0 20px 0 0}

/* hero */
.hero{position:absolute;left:0;top:112px;width:1126px;height:387px;background:radial-gradient(ellipse at 50% 45%,#3a6e3a 0%,#0d3a6e 22%,#0a2a55 50%,#071733 100%)}
.hero-caption{position:absolute;left:0;width:1126px;top:300px;text-align:center;font-family:"Play",sans-serif;font-size:30px;line-height:34px;color:#fff;text-shadow:0 2px 4px rgba(0,0,0,.8)}
.hero-arrow{position:absolute;top:159px;width:32px;height:30px;background:#2a2a2a;border:1px solid #777;display:flex;align-items:center;justify-content:center}

/* intro band */
.intro{position:absolute;left:0;top:499px;width:1126px;height:273px;background:var(--grey-bg)}
.col-title{position:absolute;font-family:"Play",sans-serif;font-weight:400;font-size:28px;color:var(--red);display:flex;align-items:center;gap:8px;border-bottom:1px solid var(--rule);padding-bottom:8px;white-space:nowrap}
.col-title b{font-weight:400;color:var(--navy)}
.welcome-text{position:absolute;left:77px;top:88px;width:340px;font-size:13.5px;line-height:19px}
.checks{position:absolute;left:77px;top:162px;list-style:none;font-size:13.5px}
.checks li{height:28px;display:flex;gap:8px;align-items:center}
.news-item{position:absolute;left:484px;width:245px;display:flex;gap:8px}
.date{width:43px;height:54px;background:var(--navy);color:#fff;text-align:center;font-size:20px;line-height:28px;flex:none}
.date small{display:block;font-size:13px;line-height:20px;border-top:1px solid #fff}
.news-item h4{font-size:12.5px;font-weight:700;margin:1px 0 4px}
.news-item p{font-size:12.5px;line-height:17.5px}
.field{position:absolute;left:801px;width:248px;background:#fff;border:1px solid #ddd;border-radius:3px;font-size:11px;color:#555;padding:5px 10px}
.submit{position:absolute;left:801px;top:212px;width:83px;height:26px;background:var(--navy);color:#fff;font-weight:700;font-size:13px;display:flex;align-items:center;justify-content:center}

/* product */
.section-title{position:absolute;left:0;width:1126px;top:798px;text-align:center;font-family:"Play",sans-serif;font-weight:400;font-size:28px;color:var(--navy)}
.section-title span{color:var(--red)}
.section-rule{position:absolute;left:400px;top:847px;width:326px;border-top:1px solid #ccc}
.section-dot{position:absolute;left:557px;top:841px;width:12px;height:12px;background:#7a94c0}
.product-frame{position:absolute;left:75px;top:887px;width:382px;height:240px;border:1px solid #ddd;background:#fff;padding:9px;box-shadow:0 10px 10px -10px rgba(0,0,0,.3)}
.product-image{width:100%;height:100%;background:linear-gradient(160deg,#2f8f2c 0%,#6aa81f 40%,#b5521a 70%,#8a1d12 100%)}
.product-name{position:absolute;left:489px;top:894px;font-family:"Play",sans-serif;font-weight:400;font-size:26px;color:var(--red)}
.product-sub{position:absolute;left:489px;top:926px;font-family:"Play",sans-serif;font-weight:400;font-size:20px;color:var(--navy)}
.product-text{position:absolute;left:490px;top:959px;width:560px;font-size:13px;line-height:20px}
.btn{position:absolute;top:1076px;width:168px;height:39px;background:var(--navy);color:#fff;font-family:"Play",sans-serif;font-weight:700;font-size:17px;display:flex;align-items:center;justify-content:center}

/* footer */
.site-footer{position:absolute;left:0;top:1159px;width:1126px;height:41px;background:var(--red);color:#fff;font-weight:700;font-size:13px}
.footer-nav{position:absolute;left:77px;top:12px}
.copyright{position:absolute;right:76px;top:12px}
</style>
</head>
<body>
<div class="canvas">

<header class="site-header">
  <div class="contact-mail">
    <svg width="17" height="11" viewBox="0 0 17 11"><rect width="17" height="11" fill="#e62129"/><path d="M0 0l8.5 6L17 0" stroke="#fff" fill="none"/></svg>
    info@vornimax.com
  </div>
  <div class="contact-phone">
    <svg width="13" height="13" viewBox="0 0 24 24"><path fill="#fff" d="M6.6 10.8a15 15 0 006.6 6.6l2.2-2.2c.3-.3.7-.4 1-.2 1.1.4 2.3.6 3.6.6.6 0 1 .4 1 1V20c0 .6-.4 1-1 1A17 17 0 013 4c0-.6.4-1 1-1h3.5c.6 0 1 .4 1 1 0 1.3.2 2.5.6 3.6.1.3 0 .7-.2 1z"/></svg>
    123-456-7890
  </div>
  <div class="brand"><span class="brand-square"></span>vornimax</div>
  <nav class="main-nav">
    <span class="home"><svg width="26" height="22" viewBox="0 0 26 22"><path d="M13 1L1 12h4v9h6v-6h4v6h6v-9h4z" fill="#e62129"/></svg></span>
    <span>About Us</span><span>Products</span><span>Company</span><span>News</span><span>Contact Us</span>
  </nav>
</header>

<section class="hero" role="img" aria-label="Close-up of a microchip on a glowing blue circuit board">
  <div class="hero-arrow" style="left:6px"><svg width="10" height="12"><path d="M8 1L2 6l6 5" stroke="#fff" stroke-width="2.5" fill="none"/></svg></div>
  <div class="hero-arrow" style="right:6px"><svg width="10" height="12"><path d="M2 1l6 5-6 5" stroke="#fff" stroke-width="2.5" fill="none"/></svg></div>
  <div class="hero-caption">High-Performance Interface Enables Early and Accurate Power<br>Profiling of Real-Time Applications</div>
</section>

<section class="intro">
  <h2 class="col-title" style="left:75px;top:32px;width:338px">
    <svg width="28" height="28" viewBox="0 0 28 28"><circle cx="14" cy="14" r="13" fill="none" stroke="#1c62a6" stroke-width="2.5"/><path d="M8 14l4 4 8-9" stroke="#ee1c25" stroke-width="2.5" fill="none"/></svg>
    Welcome to <b>Vornimax</b>
  </h2>
  <p class="welcome-text">Lorem ipsum dolor sit amet, consectetuer adipiscing elit, diam nonummy nibh euismod tincidunt ut laoreet dolore magna aliquam erat volutpat.</p>
  <ul class="checks">
    <li><svg width="14" height="12"><path d="M1 6l4 4 8-9" stroke="#e62129" stroke-width="2" fill="none"/></svg>Lorem ipsum dolor sit amet, consectetuer adipiscing</li>
    <li><svg width="14" height="12"><path d="M1 6l4 4 8-9" stroke="#e62129" stroke-width="2" fill="none"/></svg>Lorem ipsum dolor sit amet consectetuer</li>
    <li><svg width="14" height="12"><path d="M1 6l4 4 8-9" stroke="#e62129" stroke-width="2" fill="none"/></svg>Lorem ipsum dolor sit amet consectetuer adipiscing</li>
  </ul>

  <h2 class="col-title" style="left:483px;top:32px;width:247px">
    <svg width="28" height="24" viewBox="0 0 28 24"><path d="M2 9h5l12-7v20L7 15H2z" fill="#e62129"/><path d="M7 15l2 8h4l-2-8z" fill="#e62129"/><path d="M19 2l5-2v24l-5-2z" fill="#0d1f5f"/></svg>
    Latest <b>News</b>
    <span style="margin-left:auto;font-size:14px;color:#0d1f5f">‹ ›</span>
  </h2>
  <div class="news-item" style="top:92px">
    <div class="date">23<small>Jan</small></div>
    <div><h4>Duis autem vel eum iriure</h4><p>Lorem ipsum dolor sit amet, in the magnagt Lorem ipsum dolor...</p></div>
  </div>
  <div class="abs" style="left:483px;top:164px;width:247px;border-top:1px solid #e4e4e4"></div>
  <div class="news-item" style="top:183px">
    <div class="date">23<small>Jan</small></div>
    <div><h4>Duis autem vel eum iriure</h4><p>Lorem ipsum dolor sit amet, in the adipiscing magnagt Lorem ipsum ...</p></div>
  </div>

  <h2 class="col-title" style="left:801px;top:32px;width:248px">
    <svg width="32" height="28" viewBox="0 0 32 28"><path d="M2 2l14 14" stroke="#e62129" stroke-width="4"/><path d="M14 6h12v14a6 6 0 01-6 6h-4" stroke="#0d1f5f" stroke-width="2.5" fill="none"/></svg>
    Quick <b>Inquiry</b>
  </h2>
  <div class="field" style="top:92px;height:25px">Name</div>
  <div class="field" style="top:127px;height:25px">Email</div>
  <div class="field" style="top:161px;height:41px">Message</div>
  <div class="submit">SUBMIT</div>
</section>

<h2 class="section-title">About <span>Our</span> Product</h2>
<div class="section-rule"></div>
<div class="section-dot"></div>

<div class="product-frame"><div class="product-image" role="img" aria-label="Silicon wafer with glowing grid of chip dies"></div></div>
<h3 class="product-name">GridMarshal 4</h3>
<h4 class="product-sub">Reducing Dynamic Voltage Drop &amp; In-rush Current</h4>
<p class="product-text">Lorem ipsum dolor sit amet, consectetuer adipiscing elit, sed diam nonummy nibh euismod tincidunt ut laoreet dolore magna aliquam erat volutpat. Ut wisi enim ad minim veniam, quis nostrud exerci tation ullamcorper suscipit lobortis nisl ut aliquip ex ea commodo consequat.ipsum dolor sit amet, consectetuer adipiscing elit, sed diam nonummy nibh euismod tincidunt ut laoreet dolore magna aliquam erat volutpat.</p>
<div class="btn" style="left:493px">Advantages</div>
<div class="btn" style="left:673px">Product Details</div>

<footer class="site-footer">
  <div class="footer-nav">Home / About Us / Products / Company / News / Contact Us</div>
  <div class="copyright">Copyright © 2016 Vornimax. All Right Reserved.</div>
</footer>

</div>
</body>
</html>
```